BOLD & MINIMALIST DESIGN NEEDED

We want a very bold but minimalistic business card design that is impactful and utilizes both sides of the business card. Our current logo is included for your use.

We want bold fonts and good use of negative space. We don't want the logo to overpower the design.

Target Market(s)

Professionals who are building new commercial buildings.

Industry/Entity Type

Construction

Contact Information for Business Card

Name, Title, email, office phone, cell phone, website

Font styles to use
Serif
Sans Serif

Requirements
Must have
• Bold design!

```html
<!DOCTYPE html>
<html lang="en">
<head>
<meta charset="utf-8">
<title>Ridgecrest Design + Build — Business Card</title>
<link rel="stylesheet" href="https://fonts.googleapis.com/css2?family=Poppins:wght@400;500;700;800&display=swap">
<style>
  :root {
    --stage: #e6e6e6;
    --card-dark: #0b0b0b;
    --card-dark-edge: #1c1c1c;
    --card-light: #ffffff;
    --ink: #111111;
    --ink-soft: #555555;
    --rule: #333333;
    --accent: #6cc04a;
  }
  * { box-sizing: border-box; margin: 0; padding: 0; }
  html, body { width: 1200px; height: 900px; overflow: hidden; }
  body {
    background: var(--stage);
    font-family: "Poppins", sans-serif;
    color: var(--ink);
    position: relative;
  }
  .card {
    position: absolute;
    left: 285px;
    width: 630px;
    height: 360px;
    border-radius: 28px;
    box-shadow: 0 14px 30px rgba(0,0,0,0.22);
    overflow: hidden;
  }
  .card--back {
    top: 70px;
    background: radial-gradient(ellipse at 50% 45%, var(--card-dark-edge) 0%, var(--card-dark) 70%);
    display: flex;
    align-items: center;
    justify-content: center;
  }
  .card--front {
    top: 470px;
    background: linear-gradient(135deg, #f1f1f1 0%, var(--card-light) 60%);
  }
  .wordmark {
    display: flex;
    align-items: center;
    gap: 12px;
  }
  .wordmark__square {
    width: 16px;
    height: 16px;
    background: var(--accent);
    flex: none;
  }
  .wordmark__name {
    font-weight: 800;
    letter-spacing: 0.5px;
    line-height: 1.1;
    text-transform: uppercase;
  }
  .card--back .wordmark__name { color: var(--accent); font-size: 30px; }
  .card--front .wordmark {
    position: absolute;
    top: 42px;
    right: 40px;
  }
  .card--front .wordmark__name { color: var(--ink); font-size: 18px; }
  .person {
    position: absolute;
    left: 40px;
    top: 170px;
  }
  .person__name { font-size: 24px; font-weight: 800; line-height: 1.15; }
  .person__title { font-size: 17px; font-weight: 400; color: var(--ink-soft); }
  .contacts {
    position: absolute;
    left: 40px;
    top: 240px;
    display: flex;
    gap: 20px;
  }
  .contacts__col { display: flex; flex-direction: column; gap: 6px; }
  .contacts__divider { width: 1px; background: var(--rule); }
  .contact {
    display: flex;
    align-items: center;
    gap: 10px;
    font-size: 15px;
    font-weight: 500;
    color: var(--ink);
  }
  .contact svg { width: 16px; height: 16px; flex: none; }
  .address {
    position: absolute;
    left: 40px;
    right: 150px;
    top: 312px;
    border-top: 1px solid var(--rule);
    padding-top: 6px;
    font-size: 15px;
    font-weight: 500;
  }
</style>
</head>
<body>
  <section class="card card--back" aria-label="Card back">
    <div class="wordmark">
      <span class="wordmark__square"></span>
      <span class="wordmark__name">Ridgecrest Design + Build</span>
    </div>
  </section>

  <section class="card card--front" aria-label="Card front">
    <div class="wordmark">
      <span class="wordmark__square"></span>
      <span class="wordmark__name">Ridgecrest Design + Build</span>
    </div>

    <div class="person">
      <p class="person__name">Jonah Whitfield</p>
      <p class="person__title">Founder</p>
    </div>

    <div class="contacts">
      <div class="contacts__col">
        <p class="contact">
          <svg viewBox="0 0 16 16" aria-hidden="true"><rect x="4" y="1" width="8" height="14" rx="1.5" fill="none" stroke="var(--accent)" stroke-width="1.5"/><line x1="7" y1="12.5" x2="9" y2="12.5" stroke="var(--accent)" stroke-width="1.5"/></svg>
          3XX-2XX-9XXX
        </p>
        <p class="contact">
          <svg viewBox="0 0 16 16" aria-hidden="true"><path d="M3 2 L6 2 L7 5 L5.5 6.5 C6.5 8.5 7.5 9.5 9.5 10.5 L11 9 L14 10 L14 13 C8 14 2 8 3 2 Z" fill="var(--accent)"/></svg>
          555-014-2200
        </p>
      </div>
      <span class="contacts__divider"></span>
      <div class="contacts__col">
        <p class="contact">
          <svg viewBox="0 0 16 16" aria-hidden="true"><rect x="1" y="3" width="14" height="10" fill="var(--accent)"/><path d="M1 3 L8 9 L15 3" fill="none" stroke="#fff" stroke-width="1.3"/></svg>
          info@ridgecrest-db.com
        </p>
        <p class="contact">
          <svg viewBox="0 0 16 16" aria-hidden="true"><g fill="none" stroke="var(--accent)" stroke-width="1.3"><circle cx="8" cy="8" r="6.5"/><ellipse cx="8" cy="8" rx="3" ry="6.5"/><line x1="1.5" y1="8" x2="14.5" y2="8"/></g></svg>
          www.ridgecrest-db.com
        </p>
      </div>
    </div>

    <p class="address">412 Stonebrook Rd. Millbrook, GA 30500</p>
  </section>
</body>
</html>
```